Investment company needing business card

We are wanting a business card which looks sharp and easy on the eye. We are thinking of having a business card with the logo embossed on it, to really make it stand out. We will only have a small amount of information of the business card, person's name, position, email address and phone number

Contact Information for Business Card

Danielle Frost
Executive Assistant
+64 21 473 5162
danielf@harwickpartners.co.nz

Requirements
Must have
• Embossed logo
Should not have
• Not to be busy

```html
<!DOCTYPE html>
<html lang="en">
<head>
<meta charset="utf-8">
<title>Harwick Partners – Business Card</title>
<link href="https://fonts.googleapis.com/css2?family=Lato:wght@400;700;900&display=swap" rel="stylesheet">
<style>
  :root {
    --backdrop: #2e2825;
    --card: #0d0d0d;
    --card-edge: #1a1a1a;
    --accent: #2fbf7e;
    --silver: #d4d4d4;
    --text: #e6e6e6;
    --rule: #4a4a4a;
  }
  * { margin: 0; padding: 0; box-sizing: border-box; }
  html, body {
    width: 1200px;
    height: 900px;
    overflow: hidden;
    background: var(--backdrop);
    font-family: "Lato", sans-serif;
  }
  .stage {
    width: 1200px;
    height: 900px;
    display: flex;
    align-items: center;
    justify-content: center;
    gap: 44px;
  }
  .card {
    position: relative;
    width: 520px;
    height: 289px;
    background: var(--card);
    border: 1px solid var(--card-edge);
    box-shadow: 0 14px 30px rgba(0,0,0,0.45);
  }

  /* Front */
  .front .brand {
    position: absolute;
    top: 78px;
    left: 150px;
    display: flex;
    align-items: center;
    gap: 12px;
  }
  .brand-square {
    width: 30px;
    height: 30px;
    background: var(--accent);
  }
  .front .brand-name {
    font-weight: 900;
    font-size: 25px;
    letter-spacing: 1px;
    color: var(--accent);
    text-transform: uppercase;
  }
  .front .brand-rule {
    position: absolute;
    top: 122px;
    left: 150px;
    right: 34px;
    height: 1px;
    background: var(--rule);
  }
  .contact {
    position: absolute;
    left: 34px;
    bottom: 30px;
    right: 34px;
  }
  .contact-header {
    display: flex;
    align-items: center;
    gap: 14px;
  }
  .person-name {
    font-weight: 900;
    font-size: 17px;
    color: var(--accent);
    text-transform: uppercase;
    letter-spacing: 0.5px;
    white-space: nowrap;
  }
  .contact-header .rule {
    flex: 1;
    height: 1px;
    background: var(--rule);
  }
  .person-role {
    font-size: 13px;
    color: var(--text);
    margin-top: 2px;
  }
  .contact-lines {
    list-style: none;
    margin-top: 12px;
  }
  .contact-lines li {
    display: flex;
    align-items: center;
    gap: 7px;
    font-size: 13px;
    color: var(--text);
    line-height: 1.75;
  }
  .contact-lines svg { width: 11px; height: 11px; flex: none; }

  /* Back */
  .back {
    display: flex;
    align-items: center;
    justify-content: center;
    box-shadow: 0 3px 0 #161616, 0 6px 0 #111, 0 9px 0 #161616, 0 20px 34px rgba(0,0,0,0.5);
  }
  .back .brand {
    display: flex;
    align-items: center;
    gap: 14px;
  }
  .back .brand-square { background: var(--silver); width: 34px; height: 34px; }
  .back .brand-name {
    font-weight: 900;
    font-size: 28px;
    letter-spacing: 1.5px;
    color: var(--silver);
    text-transform: uppercase;
  }
</style>
</head>
<body>
<main class="stage">
  <section class="card front" aria-label="Business card front">
    <div class="brand">
      <span class="brand-square"></span>
      <span class="brand-name">Harwick Partners</span>
    </div>
    <div class="brand-rule"></div>

    <div class="contact">
      <div class="contact-header">
        <span class="person-name">Danielle Frost</span>
        <span class="rule"></span>
      </div>
      <div class="person-role">Executive Assistant</div>
      <ul class="contact-lines">
        <li>
          <svg viewBox="0 0 12 12" aria-hidden="true"><rect width="12" height="12" rx="1.5" fill="#2fbf7e"/><path d="M3.4 2.6c.4-.3.9-.2 1.1.2l.6 1.1c.2.4.1.8-.2 1l-.4.3c.4.9 1 1.5 1.9 1.9l.3-.4c.2-.3.6-.4 1-.2l1.1.6c.4.2.5.7.2 1.1l-.5.6c-.4.4-1 .5-1.6.3C5 8.3 3.7 7 3 5.1c-.2-.6-.1-1.2.3-1.6z" fill="#0d0d0d"/></svg>
          +64 21 473 5162
        </li>
        <li>
          <svg viewBox="0 0 12 12" aria-hidden="true"><rect width="12" height="12" rx="1.5" fill="#2fbf7e"/><path d="M2.5 3.5h7v5h-7z M2.5 3.5l3.5 3 3.5-3" fill="none" stroke="#0d0d0d" stroke-width="1"/></svg>
          danielf@harwickpartners.co.nz
        </li>
      </ul>
    </div>
  </section>

  <section class="card back" aria-label="Business card back">
    <div class="brand">
      <span class="brand-square"></span>
      <span class="brand-name">Harwick Partners</span>
    </div>
  </section>
</main>
</body>
</html>
```